Audio and Video download site

I am looking for a good and beautiful website where users can be a able to download and upload musicial files and video file. Basically, there will be two categories. The first category for the music files( mp3, mva and other popular music files) while the second category will be for video files (mp4, wmv, divx and other files) users would be able to like and dislike a song/video. Users do not necessarily have to sign up for them to make you or download and upload files from the website. The website should be youthful.

```html
<!DOCTYPE html>
<html lang="en">
<head>
<meta charset="utf-8">
<title>Vireo – Music and Video Files</title>
<link rel="stylesheet" href="https://fonts.googleapis.com/css2?family=Roboto:wght@300;400;500;700&display=swap">
<style>
:root{
  --blue:#2a8fd0;
  --blue-dark:#1f7dbd;
  --green:#5cb85c;
  --ink:#333333;
  --muted:#666666;
  --line:#e2e2e2;
  --panel:#f6f6f6;
  --dark:#141414;
  --band:#2f8ccb;
  --white:#ffffff;
}
*{box-sizing:border-box;margin:0;padding:0}
html,body{width:1200px;height:2675px;overflow:hidden;background:var(--white)}
body{position:relative;font-family:'Roboto',Arial,sans-serif;color:var(--ink)}
.abs{position:absolute}

/* hero */
.hero{position:absolute;left:0;top:0;width:1200px;height:637px;overflow:hidden}
.hero-photo{position:absolute;inset:0;background:linear-gradient(100deg,#2a2a2a 0%,#3d3b3a 35%,#6b5446 62%,#4a3a32 80%,#1e1b1a 100%)}
.logo{position:absolute;display:flex;align-items:center;gap:8px;font-weight:700;color:var(--white);letter-spacing:1px}
.logo-dot{width:26px;height:26px;border-radius:50%;background:var(--white)}
.hero .logo{left:98px;top:44px;font-size:34px}
.btn-signup{left:895px;top:49px;width:82px;height:26px;background:var(--blue);color:var(--white);font-size:12px;line-height:26px;text-align:center;border-radius:2px}
.btn-login{left:986px;top:49px;width:80px;height:26px;border:1px solid var(--white);color:var(--white);font-size:12px;line-height:24px;text-align:center;border-radius:2px}
.menu-icon{left:1084px;top:53px}
.hero-title{left:0;width:1200px;top:126px;text-align:center;color:var(--white);font-size:42px;font-weight:500}
.join-panel{left:435px;top:201px;width:328px;height:316px}
.field{position:absolute;left:478px;width:255px;height:43px;background:var(--white);border-radius:2px;font-size:11px;color:#777;padding-left:14px;line-height:43px}
.btn-join{left:528px;top:421px;width:142px;height:35px;background:var(--blue);color:var(--white);font-size:13px;line-height:35px;text-align:center;border-radius:2px}
.terms{left:460px;width:278px;top:474px;text-align:center;color:var(--white);font-size:11.5px;line-height:18px}
.slide-arrow{top:310px;width:32px;height:32px;border-radius:50%;background:rgba(0,0,0,.35)}

/* upload */
.upload-title{top:676px;width:487px;text-align:center;font-size:27px;color:var(--ink)}
.upload-box{top:727px;width:487px;height:329px;border:1px solid #d6d6d6;background:var(--white)}
.upload-art{position:absolute;left:168px;top:30px;width:150px;height:116px;border-radius:4px;background:linear-gradient(135deg,#2b86c9,#1c1c1c)}
.upload-types{position:absolute;left:0;width:100%;top:156px;text-align:center;font-size:13px;color:#444}
.upload-size{position:absolute;left:0;width:100%;top:182px;text-align:center;font-size:15px;color:#444}
.upload-actions{position:absolute;top:219px;left:0;width:100%;display:flex;justify-content:center;gap:15px}
.action{height:36px;border-radius:2px;color:var(--white);font-size:14px;display:flex;align-items:center;justify-content:center;gap:7px}
.action.up{width:149px;background:var(--blue)}
.action.down{width:165px;background:var(--green)}
.upload-help{position:absolute;left:0;width:100%;top:277px;text-align:center;font-size:11.5px;color:#777}

/* galleries */
.section-title{left:98px;font-size:25px;font-weight:400;color:#222;text-transform:uppercase}
.pager{display:flex;gap:6px}
.pager span{width:22px;height:22px;border:1px solid #999;border-radius:50%;display:flex;align-items:center;justify-content:center}
.card{top:0;width:230px;height:324px;border:1px solid var(--line);background:var(--white)}
.card-media{position:absolute;left:0;top:0;width:228px;height:169px}
.card-title{position:absolute;left:0;width:100%;top:184px;text-align:center;font-size:16px;color:#333}
.card-label{position:absolute;left:0;width:100%;top:213px;text-align:center;font-size:12px;color:#333}
.card-desc{position:absolute;left:0;width:100%;top:233px;text-align:center;font-size:11.5px;color:#555;line-height:18px}
.card-votes{position:absolute;left:0;bottom:0;width:228px;height:41px;background:var(--panel);border-top:1px solid var(--line);display:flex}
.vote{flex:1;display:flex;align-items:center;justify-content:center;gap:6px;font-size:13px;color:#444}
.vote+.vote{border-left:1px solid var(--line)}
.play{position:absolute;left:92px;top:62px;width:44px;height:44px;border-radius:50%;background:rgba(255,255,255,.6)}

/* app band */
.app-band{left:0;top:1532px;width:1200px;height:413px;background:linear-gradient(90deg,#0d0d0d,#2a2420 55%,#151312)}
.phone-hand{left:310px;top:60px;width:190px;height:353px;border-radius:30px 30px 0 0;background:linear-gradient(180deg,#e7e9ec,#c9a48a)}
.app-band .logo{left:581px;top:86px;font-size:30px}
.app-title{left:581px;top:136px;font-size:50px;font-weight:300;color:var(--white)}
.app-copy{left:581px;top:205px;font-size:12.5px;line-height:24px;color:var(--white)}
.store-badge{top:274px;height:54px;background:#111;border:1px solid #555;border-radius:4px}

/* subscribe */
.subscribe{left:0;top:2428px;width:1200px;height:100px;background:var(--band)}
.subscribe-copy{left:253px;top:32px;font-size:15px;line-height:22px;color:var(--white);text-transform:uppercase}
.subscribe-input{left:569px;top:20px;width:380px;height:54px;background:var(--white);border-radius:27px 0 0 27px;font-size:12px;color:#666;line-height:54px;padding-left:26px}
.subscribe-btn{left:941px;top:20px;width:125px;height:54px;background:#3a3a3a;border-radius:0 27px 27px 0;color:var(--white);font-size:12px;line-height:54px;text-align:center}

/* footer */
.social{left:0;width:1200px;top:2559px;display:flex;justify-content:center;gap:10px}
.social span{width:28px;height:28px;border-radius:50%;background:#8a8a8a}
.footer-nav{left:0;width:1200px;top:2609px;text-align:center;font-size:11px;color:#333;word-spacing:2px}
.footer-nav i{font-style:normal;margin:0 9px}
.copyright{left:0;width:1200px;top:2637px;text-align:center;font-size:11px;color:#333}
</style>
</head>
<body>

<header class="hero">
  <div class="hero-photo" role="img" aria-label="Photo of a young woman with curly hair listening to music on large headphones, eyes closed"></div>
  <div class="logo"><span>VIREO</span><span class="logo-dot"></span></div>
  <div class="abs btn-signup">SIGN UP</div>
  <div class="abs btn-login">LOGIN</div>
  <svg class="abs menu-icon" width="18" height="16" viewBox="0 0 18 16"><rect y="1" width="18" height="3" fill="#fff"/><rect y="7" width="18" height="3" fill="#fff"/><rect y="13" width="18" height="3" fill="#fff"/></svg>
  <h1 class="abs hero-title">Make life worth watching</h1>
  <svg class="abs join-panel" viewBox="0 0 328 316"><path d="M0 0H328V284L164 316L0 284Z" fill="rgba(0,0,0,.72)" stroke="rgba(255,255,255,.35)"/></svg>
  <div class="field" style="top:246px">Name *</div>
  <div class="field" style="top:301px">Password *</div>
  <div class="field" style="top:357px">Email *</div>
  <div class="abs btn-join">JOIN NOW</div>
  <p class="abs terms">By joining Vireo, you agree to our Terms of<br>Service and Privacy Policy</p>
  <svg class="abs slide-arrow" style="left:55px" viewBox="0 0 32 32"><path d="M19 10L13 16L19 22" stroke="#fff" stroke-width="2" fill="none"/></svg>
  <svg class="abs slide-arrow" style="left:1114px" viewBox="0 0 32 32"><path d="M13 10L19 16L13 22" stroke="#fff" stroke-width="2" fill="none"/></svg>
</header>

<main>
  <section class="uploads">
    <h2 class="abs upload-title" style="left:98px;font-weight:400">Select your audio file</h2>
    <h2 class="abs upload-title" style="left:615px;font-weight:400">Select your Video file</h2>

    <div class="abs upload-box" style="left:98px">
      <div class="upload-art" role="img" aria-label="Illustration of a music player screen with headphones"></div>
      <p class="upload-types">Mp3, Mva And Other Popular Music Files</p>
      <p class="upload-size">Maximum size is 15 megabytes. (mp3 files only)</p>
      <div class="upload-actions">
        <div class="action up"><svg width="13" height="13" viewBox="0 0 13 13"><path d="M6.5 1V9M3 4.5L6.5 1L10 4.5M1 12H12" stroke="#fff" stroke-width="2" fill="none"/></svg>Upload Audio</div>
        <div class="action down"><svg width="13" height="13" viewBox="0 0 13 13"><path d="M6.5 1V9M3 5.5L6.5 9L10 5.5M1 12H12" stroke="#fff" stroke-width="2" fill="none"/></svg>Download Audio</div>
      </div>
      <p class="upload-help">Have issues uploading? Tell us about it.</p>
    </div>

    <div class="abs upload-box" style="left:615px">
      <div class="upload-art" role="img" aria-label="Illustration of a film strip with a video screen"></div>
      <p class="upload-types">Mp4, Wmv, Divx And Other Files</p>
      <p class="upload-size">Maximum size is 15 megabytes. (mp3 files only)</p>
      <div class="upload-actions">
        <div class="action up"><svg width="13" height="13" viewBox="0 0 13 13"><path d="M6.5 1V9M3 4.5L6.5 1L10 4.5M1 12H12" stroke="#fff" stroke-width="2" fill="none"/></svg>Upload Video</div>
        <div class="action down"><svg width="13" height="13" viewBox="0 0 13 13"><path d="M6.5 1V9M3 5.5L6.5 9L10 5.5M1 12H12" stroke="#fff" stroke-width="2" fill="none"/></svg>Download Video</div>
      </div>
      <p class="upload-help">Have issues uploading? Tell us about it.</p>
    </div>
  </section>

  <section class="gallery music">
    <h2 class="abs section-title" style="top:1100px">Latest Music</h2>
    <div class="abs pager" style="left:1052px;top:1102px">
      <span><svg width="8" height="10" viewBox="0 0 8 10"><path d="M6 1L2 5L6 9" stroke="#777" fill="none"/></svg></span>
      <span><svg width="8" height="10" viewBox="0 0 8 10"><path d="M2 1L6 5L2 9" stroke="#777" fill="none"/></svg></span>
    </div>
    <div class="abs" style="left:0;top:1152px;width:1200px;height:324px">
      <article class="abs card" style="left:98px"><div class="card-media" role="img" aria-label="Photo of a girl dancing with headphones and light trails" style="background:linear-gradient(135deg,#3a2a20,#b0704a)"></div><h3 class="card-title" style="font-weight:400">Duis aute irure dolor</h3><p class="card-label">Music Files :</p><p class="card-desc">Mp3, Mva And Other<br>Popular Music Files</p><div class="card-votes"><span class="vote"><svg width="13" height="13" viewBox="0 0 13 13"><path d="M1 6H3V12H1ZM4 6L7 1C8 1 8.5 2 8 3.5L7.5 5H11.5C12.3 5 12.6 6 12.3 6.6L10.5 11.5C10.3 12 9.8 12 9.5 12H4Z" stroke="#444" fill="none"/></svg>Like</span><span class="vote"><svg width="13" height="13" viewBox="0 0 13 13"><path d="M1 1H3V7H1ZM4 7L7 12C8 12 8.5 11 8 9.5L7.5 8H11.5C12.3 8 12.6 7 12.3 6.4L10.5 1.5C10.3 1 9.8 1 9.5 1H4Z" stroke="#444" fill="none"/></svg>dislike</span></div></article>
      <article class="abs card" style="left:355px"><div class="card-media" role="img" aria-label="Photo of a guitarist shouting amid fire and water splashes" style="background:linear-gradient(135deg,#e89a2a,#3a6aa0)"></div><h3 class="card-title" style="font-weight:400">Duis aute irure dolor</h3><p class="card-label">Music Files :</p><p class="card-desc">Mp3, Mva And Other<br>Popular Music Files</p><div class="card-votes"><span class="vote"><svg width="13" height="13" viewBox="0 0 13 13"><path d="M1 6H3V12H1ZM4 6L7 1C8 1 8.5 2 8 3.5L7.5 5H11.5C12.3 5 12.6 6 12.3 6.6L10.5 11.5C10.3 12 9.8 12 9.5 12H4Z" stroke="#444" fill="none"/></svg>Like</span><span class="vote"><svg width="13" height="13" viewBox="0 0 13 13"><path d="M1 1H3V7H1ZM4 7L7 12C8 12 8.5 11 8 9.5L7.5 8H11.5C12.3 8 12.6 7 12.3 6.4L10.5 1.5C10.3 1 9.8 1 9.5 1H4Z" stroke="#444" fill="none"/></svg>dislike</span></div></article>
      <article class="abs card" style="left:612px"><div class="card-media" role="img" aria-label="Photo of a woman sitting with earphones in warm light" style="background:linear-gradient(135deg,#3e4a5a,#d0583a)"></div><h3 class="card-title" style="font-weight:400">Duis aute irure dolor</h3><p class="card-label">Music Files :</p><p class="card-desc">Mp3, Mva And Other<br>Popular Music Files</p><div class="card-votes"><span class="vote"><svg width="13" height="13" viewBox="0 0 13 13"><path d="M1 6H3V12H1ZM4 6L7 1C8 1 8.5 2 8 3.5L7.5 5H11.5C12.3 5 12.6 6 12.3 6.6L10.5 11.5C10.3 12 9.8 12 9.5 12H4Z" stroke="#444" fill="none"/></svg>Like</span><span class="vote"><svg width="13" height="13" viewBox="0 0 13 13"><path d="M1 1H3V7H1ZM4 7L7 12C8 12 8.5 11 8 9.5L7.5 8H11.5C12.3 8 12.6 7 12.3 6.4L10.5 1.5C10.3 1 9.8 1 9.5 1H4Z" stroke="#444" fill="none"/></svg>dislike</span></div></article>
      <article class="abs card" style="left:868px"><div class="card-media" role="img" aria-label="Photo of a smiling woman jogging outdoors with earphones" style="background:linear-gradient(135deg,#6a9a3a,#e8d8a0)"></div><h3 class="card-title" style="font-weight:400">Duis aute irure dolor</h3><p class="card-label">Music Files :</p><p class="card-desc">Mp3, Mva And Other<br>Popular Music Files</p><div class="card-votes"><span class="vote"><svg width="13" height="13" viewBox="0 0 13 13"><path d="M1 6H3V12H1ZM4 6L7 1C8 1 8.5 2 8 3.5L7.5 5H11.5C12.3 5 12.6 6 12.3 6.6L10.5 11.5C10.3 12 9.8 12 9.5 12H4Z" stroke="#444" fill="none"/></svg>Like</span><span class="vote"><svg width="13" height="13" viewBox="0 0 13 13"><path d="M1 1H3V7H1ZM4 7L7 12C8 12 8.5 11 8 9.5L7.5 8H11.5C12.3 8 12.6 7 12.3 6.4L10.5 1.5C10.3 1 9.8 1 9.5 1H4Z" stroke="#444" fill="none"/></svg>dislike</span></div></article>
    </div>
  </section>

  <section class="abs app-band" role="img" aria-label="Dark concert crowd scene with a hand holding a phone showing the app">
    <div class="abs phone-hand"></div>
    <div class="logo"><span>VIREO</span><span class="logo-dot"></span></div>
    <h2 class="abs app-title">Get the app</h2>
    <p class="abs app-copy">Never stop listening. Take your playlists and likes wherever you go.<br>Download on the Appdock Get it on PlayNest</p>
    <div class="abs store-badge" style="left:581px;width:164px"></div>
    <div class="abs store-badge" style="left:758px;width:166px"></div>
  </section>

  <section class="gallery video">
    <h2 class="abs section-title" style="top:1988px">Latest Video</h2>
    <div class="abs pager" style="left:1052px;top:1990px">
      <span><svg width="8" height="10" viewBox="0 0 8 10"><path d="M6 1L2 5L6 9" stroke="#777" fill="none"/></svg></span>
      <span><svg width="8" height="10" viewBox="0 0 8 10"><path d="M2 1L6 5L2 9" stroke="#777" fill="none"/></svg></span>
    </div>
    <div class="abs" style="left:0;top:2040px;width:1200px;height:324px">
      <article class="abs card" style="left:98px"><div class="card-media" role="img" aria-label="Photo of two laughing boys holding a camera" style="background:linear-gradient(135deg,#6a5040,#d8b040)"></div><svg class="play" viewBox="0 0 44 44"><path d="M17 13L31 22L17 31Z" fill="#fff"/></svg><h3 class="card-title" style="font-weight:400">Duis aute irure dolor</h3><p class="card-label">Video Files :</p><p class="card-desc">mp4, wmv, divx and<br>other files</p><div class="card-votes"><span class="vote"><svg width="13" height="13" viewBox="0 0 13 13"><path d="M1 6H3V12H1ZM4 6L7 1C8 1 8.5 2 8 3.5L7.5 5H11.5C12.3 5 12.6 6 12.3 6.6L10.5 11.5C10.3 12 9.8 12 9.5 12H4Z" stroke="#444" fill="none"/></svg>Like</span><span class="vote"><svg width="13" height="13" viewBox="0 0 13 13"><path d="M1 1H3V7H1ZM4 7L7 12C8 12 8.5 11 8 9.5L7.5 8H11.5C12.3 8 12.6 7 12.3 6.4L10.5 1.5C10.3 1 9.8 1 9.5 1H4Z" stroke="#444" fill="none"/></svg>dislike</span></div></article>
      <article class="abs card" style="left:355px"><div class="card-media" role="img" aria-label="Photo of a silhouetted fan cheering in a stadium" style="background:linear-gradient(180deg,#c8d0d8,#1a2a1a)"></div><svg class="play" viewBox="0 0 44 44"><path d="M17 13L31 22L17 31Z" fill="#fff"/></svg><h3 class="card-title" style="font-weight:400">Duis aute irure dolor</h3><p class="card-label">Video Files :</p><p class="card-desc">mp4, wmv, divx and<br>other files</p><div class="card-votes"><span class="vote"><svg width="13" height="13" viewBox="0 0 13 13"><path d="M1 6H3V12H1ZM4 6L7 1C8 1 8.5 2 8 3.5L7.5 5H11.5C12.3 5 12.6 6 12.3 6.6L10.5 11.5C10.3 12 9.8 12 9.5 12H4Z" stroke="#444" fill="none"/></svg>Like</span><span class="vote"><svg width="13" height="13" viewBox="0 0 13 13"><path d="M1 1H3V7H1ZM4 7L7 12C8 12 8.5 11 8 9.5L7.5 8H11.5C12.3 8 12.6 7 12.3 6.4L10.5 1.5C10.3 1 9.8 1 9.5 1H4Z" stroke="#444" fill="none"/></svg>dislike</span></div></article>
      <article class="abs card" style="left:612px"><div class="card-media" role="img" aria-label="Photo of a violinist playing in an orchestra" style="background:linear-gradient(135deg,#1a1a1a,#8a4a2a)"></div><svg class="play" viewBox="0 0 44 44"><path d="M17 13L31 22L17 31Z" fill="#fff"/></svg><h3 class="card-title" style="font-weight:400">Duis aute irure dolor</h3><p class="card-label">Video Files :</p><p class="card-desc">mp4, wmv, divx and<br>other files</p><div class="card-votes"><span class="vote"><svg width="13" height="13" viewBox="0 0 13 13"><path d="M1 6H3V12H1ZM4 6L7 1C8 1 8.5 2 8 3.5L7.5 5H11.5C12.3 5 12.6 6 12.3 6.6L10.5 11.5C10.3 12 9.8 12 9.5 12H4Z" stroke="#444" fill="none"/></svg>Like</span><span class="vote"><svg width="13" height="13" viewBox="0 0 13 13"><path d="M1 1H3V7H1ZM4 7L7 12C8 12 8.5 11 8 9.5L7.5 8H11.5C12.3 8 12.6 7 12.3 6.4L10.5 1.5C10.3 1 9.8 1 9.5 1H4Z" stroke="#444" fill="none"/></svg>dislike</span></div></article>
      <article class="abs card" style="left:868px"><div class="card-media" role="img" aria-label="Photo of a woman with an acoustic guitar against a grey wall" style="background:linear-gradient(135deg,#8a8580,#3a3532)"></div><svg class="play" viewBox="0 0 44 44"><path d="M17 13L31 22L17 31Z" fill="#fff"/></svg><h3 class="card-title" style="font-weight:400">Duis aute irure dolor</h3><p class="card-label">Video Files :</p><p class="card-desc">mp4, wmv, divx and<br>other files</p><div class="card-votes"><span class="vote"><svg width="13" height="13" viewBox="0 0 13 13"><path d="M1 6H3V12H1ZM4 6L7 1C8 1 8.5 2 8 3.5L7.5 5H11.5C12.3 5 12.6 6 12.3 6.6L10.5 11.5C10.3 12 9.8 12 9.5 12H4Z" stroke="#444" fill="none"/></svg>Like</span><span class="vote"><svg width="13" height="13" viewBox="0 0 13 13"><path d="M1 1H3V7H1ZM4 7L7 12C8 12 8.5 11 8 9.5L7.5 8H11.5C12.3 8 12.6 7 12.3 6.4L10.5 1.5C10.3 1 9.8 1 9.5 1H4Z" stroke="#444" fill="none"/></svg>dislike</span></div></article>
    </div>
  </section>

  <section class="abs subscribe">
    <svg class="abs" style="left:82px;top:22px" width="96" height="66" viewBox="0 0 96 66"><g transform="rotate(-12 48 33)" stroke="rgba(255,255,255,.22)" stroke-width="3" fill="none"><rect x="10" y="10" width="76" height="46" rx="3"/><path d="M10 12L48 38L86 12"/></g></svg>
    <svg class="abs" style="left:198px;top:31px" width="38" height="36" viewBox="0 0 38 36"><path d="M2 17L36 2L28 34L18 23ZM18 23L36 2M18 23V33L23 27" stroke="#fff" stroke-width="2.2" fill="none" stroke-linejoin="round"/></svg>
    <p class="abs subscribe-copy">Subscribe to receive updates and<br>exclusive offers.</p>
    <div class="abs subscribe-input">Enter your E - mail</div>
    <div class="abs subscribe-btn">SUBSCRIBE</div>
  </section>
</main>

<footer>
  <div class="abs social"><span></span><span></span><span></span><span></span><span></span></div>
  <nav class="abs footer-nav">HOME<i>/</i>ABOUT US<i>/</i>VIDEO FILES<i>/</i>MUSIC FILES<i>/</i>NEWS<i>/</i>CONTACT US</nav>
  <p class="abs copyright">2016 © Copyrights Vireo.All Rights Reserved</p>
</footer>

</body>
</html>
```